Velmora Consulting Business

** Please add the content information from my old business card
1. I would like to see a two sided business card with both options with the 1st Option--Tallow Spire-new WHITE BACKGROUND LOGO
2 nd Option-Tallow Spire - new BLACK- Background Logo
3rd -Option a business card with my Photo on the card
Please add the new word to the card information:
EXECUTION
AS THE OWNER'S REP
WE AIM TO ACHIEVE YOUR
INFRASTRUCTURE VISION with
OUR SPECIALIZATION & EXECUTION in:

FUNDING Planning
BUSINESS Planning
INFRASTRUCTURE Planning
PROJECT Management
Since 2012
_____________________________________________________________________
I want to get spot uv raised printing. I was liking a a nice rich white linen paper stock with black writing & NOT A COLORED CARD other than a variety of white or black cards concept

```html
<!DOCTYPE html>
<html lang="en">
<head>
<meta charset="utf-8">
<title>Velmora Consulting — Business Card</title>
<link rel="stylesheet" href="https://fonts.googleapis.com/css2?family=Arimo:wght@400;700&display=swap">
<style>
  :root {
    --stage: #1e1e1e;
    --paper: #f4f4f3;
    --ink: #1f1f1f;
    --red: #d9203a;
    --charcoal: #2a2a2b;
    --charcoal-deep: #232324;
    --white: #f2f2f2;
    --logo-muted: #4a4a4c;
  }
  * { margin: 0; padding: 0; box-sizing: border-box; }
  html, body {
    width: 1200px; height: 1059px; overflow: hidden;
    background: var(--stage);
    font-family: "Arimo", Arial, sans-serif;
  }
  .stage { position: relative; width: 1200px; height: 1059px; }

  .card { position: absolute; width: 690px; height: 392px; overflow: hidden; }

  /* Front */
  .card-front { left: 256px; top: 89px; background: var(--paper); color: var(--ink); }
  .brand-front {
    position: absolute; right: 38px; top: 212px; transform: translateY(-100%);
    text-align: right; color: var(--ink); font-weight: 700;
  }
  .brand-front .brand-name { font-size: 48px; line-height: 1; display: block; }
  .brand-front .brand-sub { font-size: 12px; letter-spacing: 10px; margin-right: -10px; display: block; margin-top: 8px; }
  .person-name {
    position: absolute; left: 38px; top: 190px;
    font-size: 24px; font-weight: 700; color: var(--red);
  }
  .person-title { position: absolute; left: 38px; top: 222px; font-size: 15.5px; letter-spacing: .2px; }
  .divider { position: absolute; left: 38px; right: 38px; top: 260px; height: 1px; background: var(--ink); }
  .contact-list { position: absolute; left: 38px; top: 282px; list-style: none; }
  .contact-list li { display: flex; align-items: center; height: 25.5px; font-size: 16.5px; }
  .contact-list svg { width: 12px; height: 12px; margin-right: 8px; fill: var(--red); }
  .locations { position: absolute; right: 38px; top: 333px; font-size: 16.5px; }
  .footer-band { position: absolute; left: 0; bottom: 0; width: 100%; height: 15px; }

  /* Back */
  .card-back {
    left: 253px; top: 546px; height: 395px;
    background: linear-gradient(90deg, var(--charcoal-deep), var(--charcoal) 50%, var(--charcoal-deep));
    color: var(--white); text-align: center;
  }
  .brand-back { position: absolute; left: 0; right: 0; top: 58px; color: var(--logo-muted); font-weight: 700; }
  .brand-back .brand-name { font-size: 62px; line-height: 1; display: block; }
  .brand-back .brand-sub { font-size: 17px; letter-spacing: 17px; margin-right: -17px; display: block; margin-top: 10px; }
  .tagline { position: absolute; left: 0; right: 0; top: 164px; font-size: 18px; line-height: 30.5px; }
  .tagline .lead { color: var(--red); display: block; }
  .rule { position: absolute; left: 0; right: 0; height: 1.5px; background: var(--red); }
  .rule-top { top: 259px; }
  .rule-bottom { top: 356px; }
  .services { position: absolute; left: 0; right: 0; top: 274px; font-size: 18px; line-height: 32px; }
  .services .sep { color: var(--red); margin: 0 6px; }
  .since {
    position: absolute; left: 50%; top: 344px; transform: translateX(-50%);
    padding: 0 9px; height: 25px; line-height: 23px;
    border: 1.5px solid var(--red); border-radius: 13px;
    background: var(--charcoal); font-size: 18px;
  }
</style>
</head>
<body>
<main class="stage">

  <section class="card card-front" aria-label="Business card front">
    <div class="brand-front">
      <span class="brand-name">Velmora</span>
      <span class="brand-sub">CONSULTING</span>
    </div>
    <h1 class="person-name">Marisol Hartwell-Okafor</h1>
    <p class="person-title">CEO / LEAD PROJECT MANAGER</p>
    <div class="divider"></div>
    <ul class="contact-list">
      <li><svg viewBox="0 0 12 12"><path d="M1 4c0-2 2-3 5-3s5 1 5 3v1H8V4H4v1H1zM2 6h8l1 5H1z"/></svg>867.555.0142</li>
      <li><svg viewBox="0 0 12 12"><path d="M1 4l5-3 5 3v7H1zM2 5l4 3 4-3"/></svg>marisol@velmora.ca</li>
      <li><svg viewBox="0 0 12 12"><circle cx="6" cy="6" r="5.5"/></svg>www.velmora.ca</li>
    </ul>
    <p class="locations">Harrowmere NT • Lindqvist NB</p>
    <svg class="footer-band" viewBox="0 0 690 15" preserveAspectRatio="none" aria-hidden="true">
      <rect width="690" height="15" fill="#2a2a2b"/>
      <polygon points="0,0 340,0 325,15 0,15" fill="#d9203a"/>
      <polygon points="355,0 364,0 336,15 327,15" fill="#f4f4f3"/>
    </svg>
  </section>

  <section class="card card-back" aria-label="Business card back">
    <div class="brand-back">
      <span class="brand-name">Velmora</span>
      <span class="brand-sub">CONSULTING</span>
    </div>
    <p class="tagline">
      <span class="lead">AS THE OWNER'S REP</span>
      WE AIM TO ACHIEVE YOUR INFRASTRUCTURE VISION<br>
      with OUR SPECIALIZATION &amp; EXECUTION in:
    </p>
    <div class="rule rule-top"></div>
    <p class="services">
      FUNDING Planning<span class="sep">|</span>BUSINESS Planning<br>
      INFRASTRUCTURE Planning<span class="sep">|</span>PROJECT Management
    </p>
    <div class="rule rule-bottom"></div>
    <p class="since">Since 2012</p>
  </section>

</main>
</body>
</html>
```